Task Force Silver Owls Deployment Poster

Looking for a design to represent an Army Aviation Task Force. The unit is known as the Silver Owls based out of Fort Marrow, Texas and consists of RQ-27K Pellar Helicopters, VT-38B Corvane Helicopters, SL-92R Stormjay Helicopters, and PX-14N MEDEVAC Helicopters. The unit will be deploying to Afghanistan in 2019 to support Operation Harbor's Lantern. The individual companies that make up our formation are "TIDEWATER - RED FOXES - STONE WARDEN - GRANITE SHIELD - DEEP ROOT - REDTHISTLE - ORBIT – HERON SKYLIFT – LODESTAR – SANDGLASS – TALL PINES" The unit patch is attached for reference.

Industry/Entity Type

Army

Font styles to use
Sans Serif

Colors

Designer to choose colors to be used in the design.

Requirements
Must have
• Must include "Operation Harbor's Lantern 2019" and the unit names
Nice to have
• If able, incorporate the El Paso star somehow (star on the side of the mountain)
Should not have
• No bright/vibrant colors or political statements

```html
<!DOCTYPE html>
<html lang="en">
<head>
<meta charset="utf-8">
<title>Task Force Silver Owls – Operation Harbor's Lantern 2019</title>
<link href="https://fonts.googleapis.com/css2?family=Stardos+Stencil:wght@700&family=Big+Shoulders+Stencil+Display:wght@800&family=Oswald:wght@600&display=swap" rel="stylesheet">
<style>
  :root {
    --rust-dark: #3a2410;
    --rust-mid: #7a4a1e;
    --rust-light: #b27a3a;
    --glow: #f1d79a;
    --cream: #f3e2bb;
    --ink: #1c120a;
    --patch-cream: #e9d3a0;
  }
  * { margin: 0; padding: 0; box-sizing: border-box; }
  html, body { width: 849px; height: 1200px; overflow: hidden; background: var(--ink); }
  .poster {
    position: relative;
    width: 849px; height: 1200px; overflow: hidden;
    background:
      radial-gradient(ellipse 340px 420px at 424px 650px, rgba(241,215,154,.5), rgba(241,215,154,0) 72%),
      radial-gradient(ellipse 600px 500px at 424px 300px, var(--rust-light), rgba(178,122,58,0) 75%),
      linear-gradient(180deg, var(--rust-mid) 0%, #8c5a26 40%, #5e3815 78%, var(--rust-dark) 100%);
  }
  .aircraft { position: absolute; }
  .aircraft--left { left: 0; top: 0; width: 290px; height: 376px;
    background: radial-gradient(ellipse at 40% 45%, #5a4630 0%, rgba(40,28,16,.85) 50%, rgba(40,28,16,0) 75%); }
  .aircraft--right { right: 0; top: 0; width: 230px; height: 420px;
    background: radial-gradient(ellipse at 65% 45%, #5a4630 0%, rgba(40,28,16,.85) 50%, rgba(40,28,16,0) 75%); }

  .title {
    position: absolute; left: 0; width: 100%; text-align: center; white-space: nowrap;
    font-family: "Stardos Stencil", serif; font-weight: 700;
    color: var(--cream);
    text-shadow: 0 2px 0 var(--rust-dark), 0 0 12px rgba(60,30,10,.6);
    line-height: 1;
  }
  .title--top { top: 38px; font-size: 96px; transform: scaleX(.7); }
  .title--main { top: 172px; font-size: 82px; transform: scaleX(.84); }

  .unit-mark {
    position: absolute; left: 150px; top: 430px; width: 549px; height: 440px;
    display: flex; flex-direction: column; align-items: center; gap: 24px;
  }
  .unit-mark__name {
    font-family: "Oswald", sans-serif; font-weight: 600; font-size: 50px; line-height: 1;
    letter-spacing: 5px; color: var(--ink);
  }
  .unit-mark__dot { width: 330px; height: 330px; border-radius: 50%; background: var(--patch-cream); }

  .company-list { position: absolute; top: 736px; width: 250px; list-style: none; }
  .company-list--left { left: 0; }
  .company-list--right { right: 0; }
  .company {
    height: 72px; display: flex; align-items: center; justify-content: center;
    font-family: "Big Shoulders Stencil Display", sans-serif; font-weight: 800; font-size: 31px;
    color: var(--cream); letter-spacing: .5px; white-space: nowrap;
    text-shadow: 0 2px 2px var(--rust-dark);
    background: linear-gradient(90deg, rgba(243,226,187,0) 0%, rgba(243,226,187,.14) 30%, rgba(243,226,187,.14) 70%, rgba(243,226,187,0) 100%) center / 100% 30px no-repeat;
  }

  .year {
    position: absolute; left: 0; width: 100%; top: 918px; text-align: center;
    font-family: "Big Shoulders Stencil Display", sans-serif; font-weight: 800; font-size: 196px;
    color: var(--cream); line-height: 1;
    text-shadow: 0 3px 0 var(--rust-dark), 0 0 20px rgba(40,20,8,.6);
  }
</style>
</head>
<body>
<main class="poster">
  <div class="aircraft aircraft--left" role="img" aria-label="Attack helicopter seen from below with rocket pods"></div>
  <div class="aircraft aircraft--right" role="img" aria-label="Second attack helicopter seen from below with missiles"></div>

  <h1>
    <span class="title title--top">OPERATION</span>
    <span class="title title--main">HARBOR´S LANTERN</span>
  </h1>

  <div class="unit-mark">
    <span class="unit-mark__name">TF SILVER OWLS</span>
    <span class="unit-mark__dot"></span>
  </div>

  <ul class="company-list company-list--left">
    <li class="company">TIDEWATER</li>
    <li class="company">RED FOXES</li>
    <li class="company">STONE WARDEN</li>
    <li class="company">GRANITE SHIELD</li>
    <li class="company">DEEP ROOT</li>
    <li class="company">REDTHISTLE</li>
  </ul>

  <ul class="company-list company-list--right">
    <li class="company">ORBIT</li>
    <li class="company">HERON</li>
    <li class="company">SKYLIFT</li>
    <li class="company">LODESTAR</li>
    <li class="company">SANDGLASS</li>
    <li class="company">TALL PINES</li>
  </ul>

  <div class="year">2019</div>
</main>
</body>
</html>
```